Marrowby Water Taxi and Transport Business Card

I need business cards for my new water taxi and freight transport business I have started here in Kodiak Alaska. Kodiak is a remote island in the middle of the gulf of Alaska. There are seven native villages around the island and Kodiak is the #2 fishing port in the United States. We also have the largest Coast Guard Base in the U.S. My company will be providing water taxi and freight transport logistics to the villages and many hunting and fishing lodges as well as remote properties around the island.

I would like a business card that isn't status quo, something that stands out, either in feel or appearance. I do like clean minimal designs but it needs to have the necessary contact info on it.

Target Market(s)

remote lodge / property owners, residents of the many villages around Kodiak and any one wanting to enjoy the great outdoors of Kodiak Alaska

Industry/Entity Type

Business

Contact Information for Business Card

I like clean simple designs that aren't cluttered but still provide the necessary information

Colors
0255a3
3277b5
33a4d5
9bcb3c
add136
fbed22
ffc214
f78f20
f37122

Requirements
Must have
• logo and contact info
• Captain Mason Elwick
• www.marrowbyferryline.com
• mason@marrowbyferryline.com

```html
<!DOCTYPE html>
<html lang="en">
<head>
<meta charset="utf-8">
<title>Marrowby Water Taxi &amp; Transport – Business Card</title>
<link rel="stylesheet" href="https://fonts.googleapis.com/css2?family=Open+Sans:wght@300;400;700;800&display=swap">
<style>
  :root {
    --page-bg: #ebeced;
    --card-bg: #ffffff;
    --navy: #1157a5;
    --brand-blue: #0255a3;
    --sky-blue: #33a4d5;
    --light-wave: #5cc0ea;
    --ink-dark: #3a3020;
    --white: #ffffff;
  }
  * { box-sizing: border-box; margin: 0; padding: 0; }
  html, body {
    width: 1082px; height: 1200px; overflow: hidden;
    background: var(--page-bg);
    font-family: "Open Sans", Arial, sans-serif;
  }
  .card {
    position: absolute;
    background: var(--card-bg);
    overflow: hidden;
    box-shadow: 0 4px 10px rgba(0,0,0,0.12);
  }
  .card--front { left: 133px; top: 102px; width: 783px; height: 456px; }
  .card--back  { left: 128px; top: 632px; width: 784px; height: 458px; }
  .card__waves { position: absolute; left: 0; top: 0; width: 100%; height: 100%; }

  .front__mark {
    position: absolute; left: 346px; top: 110px;
    width: 92px; height: 92px; border-radius: 50%;
    background: var(--sky-blue);
  }
  .front__name {
    position: absolute; left: 0; right: 0; top: 231px;
    text-align: center; line-height: 1;
    font-weight: 800; font-size: 84px; letter-spacing: 2px;
    color: var(--brand-blue);
  }
  .front__tagline {
    position: absolute; left: 0; right: 0; top: 379px;
    text-align: center; line-height: 1;
    font-weight: 300; font-size: 46px; letter-spacing: 1px;
    color: var(--white);
  }

  .back__brand {
    position: absolute; left: 506px; top: 127px; width: 270px;
    text-align: center;
  }
  .back__name {
    font-weight: 800; font-size: 40px; letter-spacing: 1px;
    color: var(--brand-blue); line-height: 1;
  }
  .back__tag {
    margin-top: 4px;
    font-weight: 400; font-size: 16px; line-height: 1.1; color: var(--ink-dark);
  }
  .back__person {
    position: absolute; left: 63px; top: 166px;
    font-weight: 700; font-size: 24px; line-height: 1.2; color: var(--navy);
  }
  .back__photo {
    position: absolute; left: 479px; top: 232px; right: 0; bottom: 0;
    background:
      linear-gradient(90deg, var(--navy) 0%, rgba(17,87,165,0) 32%),
      linear-gradient(180deg, #5e9cd8 0%, #a8cbe9 32%, #3a7cbb 42%, #1f62a6 70%, #8fb6dc 100%);
  }
  .contact {
    position: absolute; left: 60px; top: 287px;
    list-style: none;
  }
  .contact__item {
    display: flex; align-items: center; gap: 8px;
    height: 35px;
    font-weight: 700; font-size: 24px; color: var(--white);
  }
  .contact__icon { width: 22px; height: 22px; flex: none; }
</style>
</head>
<body>

<section class="card card--front" aria-label="Card front">
  <svg class="card__waves" viewBox="0 0 783 456" aria-hidden="true">
    <path d="M0 340 C 200 326, 600 324, 783 334 C 600 332, 200 336, 0 348 Z" fill="var(--light-wave)"/>
    <path d="M190 332 C 300 322, 480 322, 580 328 C 480 326, 300 328, 190 336 Z" fill="var(--sky-blue)"/>
    <path d="M0 356 C 250 344, 550 344, 783 352 L783 456 L0 456 Z" fill="var(--navy)"/>
  </svg>
  <div class="front__mark" aria-hidden="true"></div>
  <div class="front__name">MARROWBY</div>
  <div class="front__tagline">Water Taxi &amp; Transport</div>
</section>

<section class="card card--back" aria-label="Card back">
  <div class="back__photo" role="img" aria-label="Photo of a water taxi boat cruising on open water with mountains on the horizon"></div>
  <svg class="card__waves" viewBox="0 0 784 458" aria-hidden="true">
    <path d="M0 226 C 200 212, 600 210, 784 218 C 600 216, 200 220, 0 232 Z" fill="var(--light-wave)"/>
    <path d="M220 216 C 330 206, 500 206, 600 212 C 500 210, 330 212, 220 220 Z" fill="var(--sky-blue)"/>
    <path d="M0 238 C 200 226, 560 222, 784 230 L784 232 L479 232 L479 458 L0 458 Z" fill="var(--navy)"/>
  </svg>

  <div class="back__brand">
    <div class="back__name">MARROWBY</div>
    <div class="back__tag">Water Taxi &amp; Transport</div>
  </div>

  <div class="back__person">Captain Mason Elwick</div>

  <ul class="contact">
    <li class="contact__item">
      <svg class="contact__icon" viewBox="0 0 22 22" aria-hidden="true">
        <rect x="5" y="2" width="12" height="18" rx="2" fill="none" stroke="#fff" stroke-width="1.6"/>
        <line x1="9" y1="17" x2="13" y2="17" stroke="#fff" stroke-width="1.6"/>
      </svg>
      907-555-0148
    </li>
    <li class="contact__item">
      <svg class="contact__icon" viewBox="0 0 22 22" aria-hidden="true">
        <rect x="2" y="5" width="18" height="12" fill="none" stroke="#fff" stroke-width="1.6"/>
        <polyline points="2,5 11,12 20,5" fill="none" stroke="#fff" stroke-width="1.6"/>
      </svg>
      mason@marrowbyferryline.com
    </li>
    <li class="contact__item">
      <svg class="contact__icon" viewBox="0 0 22 22" aria-hidden="true">
        <circle cx="11" cy="11" r="9" fill="none" stroke="#fff" stroke-width="1.5"/>
        <ellipse cx="11" cy="11" rx="4" ry="9" fill="none" stroke="#fff" stroke-width="1.3"/>
        <line x1="2" y1="11" x2="20" y2="11" stroke="#fff" stroke-width="1.3"/>
        <line x1="4" y1="6" x2="18" y2="6" stroke="#fff" stroke-width="1.1"/>
        <line x1="4" y1="16" x2="18" y2="16" stroke="#fff" stroke-width="1.1"/>
      </svg>
      www.marrowbyferryline.com
    </li>
  </ul>
</section>

</body>
</html>
```